Small Business Broker Business Card Design

A business card design for a small business brokerage, which is a financial service, not unlike real estate brokerage, but for small businesses such as laundromats, pizza shops, restaurants, cleaners etc. The designs should all be simple, more conservative in nature, using the colors and font of the logo. Again, think real estate Brokerage as a business context
Contact Information for Business Card
Name: Glen R. Harlow. Title: Small Business Advisor. Email: g.harlow@bayfieldcapitalworks.example. Mobile: (555) 274-3918. Office: (555) 806-2147. www.bayfieldcapitalworks.example

```html
<!DOCTYPE html>
<html lang="en">
<head>
<meta charset="utf-8">
<title>Bayfield Capital Works – Business Card</title>
<link rel="stylesheet" href="https://fonts.googleapis.com/css2?family=Montserrat:wght@400;500;700;800&display=swap">
<style>
  :root {
    --navy: #1a3866;
    --navy-light: #24477a;
    --green: #8cc63f;
    --white: #ffffff;
    --backdrop: #2a2c30;
  }
  * { margin: 0; padding: 0; box-sizing: border-box; }
  html, body { width: 1200px; height: 900px; overflow: hidden; }
  body {
    background: var(--backdrop);
    font-family: "Montserrat", Arial, sans-serif;
    color: var(--white);
    position: relative;
  }
  .card {
    position: absolute;
    left: 250px;
    width: 700px;
    height: 400px;
    background: var(--navy);
    border-bottom: 5px solid var(--green);
    overflow: hidden;
  }
  .card--front { top: 40px; }
  .card--back { top: 460px; }
  .card__bands { position: absolute; inset: 0; }

  .brand { position: absolute; text-align: left; white-space: nowrap; }
  .brand__name {
    display: flex; align-items: center; gap: 12px;
    font-weight: 800; text-transform: uppercase; color: var(--white);
    letter-spacing: 0.03em;
  }
  .brand__mark { background: var(--green); flex: none; }
  .brand__tagline {
    color: var(--green); font-weight: 700; text-transform: uppercase;
    letter-spacing: 0.06em; margin-top: 6px;
  }
  .card--front .brand { left: 50%; top: 50%; transform: translate(-50%, -50%); }
  .card--front .brand__name { font-size: 27px; }
  .card--front .brand__mark { width: 20px; height: 20px; }
  .card--front .brand__tagline { font-size: 13px; padding-left: 32px; }

  .card--back .brand { right: 44px; top: 46px; }
  .card--back .brand__name { font-size: 15px; gap: 8px; }
  .card--back .brand__mark { width: 12px; height: 12px; }
  .card--back .brand__tagline { font-size: 8px; padding-left: 20px; }

  .person { position: absolute; left: 44px; top: 40px; }
  .person__name {
    color: var(--green); font-weight: 800; font-size: 28px;
    text-transform: uppercase; letter-spacing: 0.03em; white-space: nowrap;
  }
  .person__title { font-size: 15px; margin-top: 2px; }
  .divider {
    position: absolute; left: 44px; right: 44px; top: 118px;
    height: 1px; background: var(--green);
  }
  .contacts { position: absolute; left: 44px; top: 146px; list-style: none; }
  .contacts li {
    display: flex; align-items: center; gap: 12px;
    font-size: 14px; line-height: 30px; white-space: nowrap;
  }
  .contacts svg { width: 14px; height: 14px; fill: var(--green); flex: none; }
  .address {
    position: absolute; right: 44px; bottom: 36px;
    text-align: right; font-size: 15px; line-height: 24px; font-style: normal;
  }
</style>
</head>
<body>

<section class="card card--front" aria-label="Card front">
  <svg class="card__bands" viewBox="0 0 700 400" preserveAspectRatio="none" aria-hidden="true">
    <polygon points="0,60 700,140 700,210 0,130" fill="var(--navy-light)"/>
    <polygon points="0,250 700,330 700,400 0,400 0,320" fill="var(--navy-light)" opacity="0.7"/>
    <polygon points="380,0 470,0 700,260 700,360" fill="var(--navy-light)" opacity="0.6"/>
  </svg>
  <div class="brand">
    <div class="brand__name"><span class="brand__mark"></span>Bayfield Capital Works, Inc</div>
    <div class="brand__tagline">Main street deals, guided with care</div>
  </div>
</section>

<section class="card card--back" aria-label="Card back">
  <div class="person">
    <h1 class="person__name">Glen R. Harlow</h1>
    <p class="person__title">Small Business Advisor</p>
  </div>
  <div class="brand">
    <div class="brand__name"><span class="brand__mark"></span>Bayfield Capital Works, Inc</div>
    <div class="brand__tagline">Main street deals, guided with care</div>
  </div>
  <div class="divider"></div>
  <ul class="contacts">
    <li><svg viewBox="0 0 24 24" aria-hidden="true"><path d="M6.6 10.8a15 15 0 0 0 6.6 6.6l2.2-2.2a1 1 0 0 1 1-.25 11.4 11.4 0 0 0 3.6.57 1 1 0 0 1 1 1V20a1 1 0 0 1-1 1A17 17 0 0 1 3 4a1 1 0 0 1 1-1h3.5a1 1 0 0 1 1 1c0 1.25.2 2.45.57 3.57a1 1 0 0 1-.25 1z"/></svg>(555) 274-3918</li>
    <li><svg viewBox="0 0 24 24" aria-hidden="true"><path d="M7 1h10a2 2 0 0 1 2 2v18a2 2 0 0 1-2 2H7a2 2 0 0 1-2-2V3a2 2 0 0 1 2-2zm0 3v14h10V4zm5 15.5a1 1 0 1 0 0 2 1 1 0 0 0 0-2z"/></svg>(555) 806-2147</li>
    <li><svg viewBox="0 0 24 24" aria-hidden="true"><path d="M2 5h20v14H2zm2 2v.5l8 5 8-5V7zm0 2.8V17h16V9.8l-8 5z"/></svg>g.harlow@bayfieldcapitalworks.example</li>
    <li><svg viewBox="0 0 24 24" aria-hidden="true"><path d="M12 2a10 10 0 1 0 0 20 10 10 0 0 0 0-20zm6.9 6h-3a15 15 0 0 0-1.3-4A8 8 0 0 1 18.9 8zM12 4c.8 1.2 1.5 2.5 1.9 4h-3.8c.4-1.5 1.1-2.8 1.9-4zM4.3 14a8 8 0 0 1 0-4h3.4a16 16 0 0 0 0 4zm.8 2h3a15 15 0 0 0 1.3 4A8 8 0 0 1 5.1 16zm3-8h-3a8 8 0 0 1 4.3-4 15 15 0 0 0-1.3 4zM12 20c-.8-1.2-1.5-2.5-1.9-4h3.8c-.4 1.5-1.1 2.8-1.9 4zm2.3-6H9.7a14 14 0 0 1 0-4h4.6a14 14 0 0 1 0 4zm.3 6a15 15 0 0 0 1.3-4h3a8 8 0 0 1-4.3 4zm1.7-6a16 16 0 0 0 0-4h3.4a8 8 0 0 1 0 4z"/></svg>www.bayfieldcapitalworks.example</li>
  </ul>
  <address class="address">P.O. Box 2218 Alder Street<br>Westbrook Falls, NY 12745</address>
</section>

</body>
</html>
```